Flyer design for commercial marketing

Looking to get a flyer design to email out to companies indicating our services
Company Name - Quillmark Networks
Company Logo - (Attached)
Services Offered
FULL HD DIGITAL IP CCTV SYSTEMS
IP ACCESS CONTROL SYSTEMS RFID / BIOMETRIC
IP EMPLOYEE MANAGEMENT SYSTEMS RFID / BIOMETRIC
NETWORKING / FIBER OPTIC SOLUTIONS
The designer can input necessary text and images
It is up to the designer to put images. I dont want the flyer too tacky. I am using this for commercial advertising
Updates
Target Market(s)
Corporate
Industry/Entity Type
It Company
Look and feel
Each slider illustrates characteristics of the customer's brand and the style your logo design should communicate.

```html
<!DOCTYPE html>
<html lang="en">
<head>
<meta charset="utf-8">
<title>Quillmark Networks – Services Flyer</title>
<link href="https://fonts.googleapis.com/css2?family=Oswald:wght@400;500;700&family=Open+Sans:wght@400;600;700&display=swap" rel="stylesheet">
<style>
  :root {
    --blue: #1a7fe0;
    --blue-light: #3aa0f5;
    --dark: #2b2d31;
    --darker: #1f2023;
    --ink: #33363b;
    --white: #ffffff;
    --photo-sky: #9fb8cf;
    --photo-glass: #5d7c98;
    --photo-grey: #c9ccd0;
  }
  html, body { margin: 0; padding: 0; overflow: hidden; }
  body { width: 900px; height: 1200px; background: var(--white); }
  .flyer { position: relative; width: 900px; height: 1200px; overflow: hidden; background: var(--white); font-family: "Open Sans", sans-serif; color: var(--ink); }
  .backdrop { position: absolute; inset: 0; }

  .building-photo { position: absolute; left: 460px; top: 0; width: 440px; height: 340px; background: linear-gradient(160deg, var(--photo-sky), var(--photo-glass) 70%, #46617a); }
  .phone-photo { position: absolute; left: 575px; top: 120px; width: 190px; height: 350px; border-radius: 28px; background: linear-gradient(180deg, #3b3f45, #1c1e21); box-shadow: 0 8px 20px rgba(0,0,0,.3); }
  .camera-photo { position: absolute; left: 345px; top: 520px; width: 250px; height: 250px; border-radius: 50%; background: radial-gradient(circle at 45% 40%, #f4f5f6, var(--photo-grey) 60%, #8f959c); border: 10px solid var(--blue); box-sizing: border-box; }
  .reader-photo { position: absolute; left: 180px; top: 915px; width: 130px; height: 160px; border-radius: 10px; background: linear-gradient(180deg, #4a4d52, #1e2024); }

  .brand { position: absolute; left: 36px; top: 34px; display: flex; align-items: center; gap: 16px; }
  .brand-mark { width: 74px; height: 74px; border-radius: 50%; background: var(--blue); flex: none; }
  .brand-name { font-family: "Oswald", sans-serif; font-weight: 500; color: var(--blue); text-transform: uppercase; letter-spacing: 1px; line-height: 1; }
  .brand-name .brand-line1 { display: block; font-size: 44px; }
  .brand-name .brand-line2 { display: block; font-size: 21px; margin-top: 4px; }

  .headline { position: absolute; left: 36px; top: 296px; margin: 0; font-family: "Oswald", sans-serif; text-transform: uppercase; font-weight: 500; }
  .headline-small { display: block; font-size: 34px; line-height: 46px; font-weight: 500; color: var(--ink); }
  .headline-big { display: block; font-size: 66px; font-weight: 700; color: var(--blue); line-height: 74px; }
  .intro { position: absolute; left: 36px; top: 436px; width: 290px; font-size: 14px; line-height: 21px; margin: 0; color: var(--ink); }

  .features { position: absolute; left: 36px; top: 700px; width: 300px; }
  .features h3 { margin: 0 0 10px; font-family: "Oswald", sans-serif; font-size: 28px; font-weight: 500; line-height: 1.1; color: var(--blue); text-transform: uppercase; }
  .features ul { margin: 0; padding: 0; list-style: none; font-size: 14px; line-height: 21px; }
  .features li::before { content: ""; display: inline-block; width: 7px; height: 7px; border-radius: 50%; background: var(--blue); margin-right: 8px; vertical-align: middle; }

  .services { position: absolute; left: 540px; top: 725px; width: 340px; color: var(--white); }
  .services h2 { margin: 0 0 18px; font-family: "Oswald", sans-serif; font-size: 40px; line-height: 1.1; font-weight: 500; text-transform: uppercase; letter-spacing: 1px; }
  .services ul { margin: 0; padding: 0; list-style: none; font-size: 13px; font-weight: 600; line-height: 20px; text-transform: uppercase; }
  .services li { margin-bottom: 8px; padding-left: 17px; text-indent: -17px; }
  .services li::before { content: ""; display: inline-block; width: 7px; height: 7px; border-radius: 50%; background: var(--blue-light); margin-right: 10px; vertical-align: middle; text-indent: 0; }
  .service-icons { display: flex; gap: 24px; margin-top: 24px; }
  .service-icons svg { width: 42px; height: 42px; }

  .web { position: absolute; left: 300px; top: 1126px; display: flex; align-items: center; gap: 16px; font-size: 30px; font-weight: 600; color: var(--white); }
  .web svg { width: 40px; height: 40px; }
</style>
</head>
<body>
<main class="flyer">
  <svg class="backdrop" viewBox="0 0 900 1200" width="900" height="1200" aria-hidden="true">
    <path d="M900 470 C720 520 540 600 440 720 L420 1120 L900 1120 Z" fill="var(--dark)"/>
    <path d="M900 450 C720 505 540 585 430 710" fill="none" stroke="var(--blue)" stroke-width="16"/>
    <path d="M0 1120 C300 1070 620 1100 900 1060 L900 1200 L0 1200 Z" fill="var(--darker)"/>
    <path d="M0 1112 C300 1062 620 1092 900 1052" fill="none" stroke="var(--blue)" stroke-width="14"/>
  </svg>

  <div class="building-photo" role="img" aria-label="Modern glass office building against the sky"></div>
  <svg class="backdrop" viewBox="0 0 900 1200" width="900" height="1200" aria-hidden="true">
    <path d="M440 0 C470 120 430 260 520 350 C640 420 780 330 900 350 L900 360 C780 345 630 440 505 360 C420 270 455 120 425 0 Z" fill="var(--blue)"/>
    <path d="M425 0 C455 120 420 270 505 360 C630 440 780 345 900 360 L900 380 C780 370 620 460 490 375 C400 280 440 120 405 0 Z" fill="var(--white)"/>
  </svg>
  <div class="phone-photo" role="img" aria-label="Hand holding a smartphone showing live security camera feeds"></div>
  <div class="camera-photo" role="img" aria-label="Dome and bullet security cameras"></div>
  <div class="reader-photo" role="img" aria-label="Biometric fingerprint access control terminal"></div>

  <header class="brand">
    <span class="brand-mark" aria-hidden="true"></span>
    <span class="brand-name"><span class="brand-line1">Quillmark</span><span class="brand-line2">Networks</span></span>
  </header>

  <h1 class="headline">
    <span class="headline-small">Lorem Ipsum Is Simply</span>
    <span class="headline-big">Dummy Text</span>
  </h1>
  <p class="intro">Contrary to common belief, this sample text is not simply random. It has roots in a classical piece of literature, making it well over two thousand years old. Scholars studying the passage traced one of its more obscure words through many later works and found the original source. The text comes from an old treatise on the extremes of good and evil, written long ago, and it has served printers for centuries.</p>

  <section class="features">
    <h3>Lorem Ipsum<br>Dolor Sit Amet:</h3>
    <ul>
      <li>In pretium dolor ut nibh consectet</li>
      <li>Cras tempor velit eu sapien</li>
      <li>Mauris in quam molestie</li>
      <li>Pellentesque a ligula in mauris</li>
      <li>Sed vel dolor auctor nisl</li>
      <li>Pellentesque iaculis</li>
    </ul>
  </section>

  <section class="services">
    <h2>Our Services</h2>
    <ul>
      <li>Full HD Digital IP CCTV Systems</li>
      <li>IP Access Control Systems RFID / Biometric</li>
      <li>IP Employee Management Systems RFID / Biometric</li>
      <li>Networking / Fiber Optic Solutions</li>
    </ul>
    <div class="service-icons" aria-hidden="true">
      <svg viewBox="0 0 44 44"><rect x="8" y="4" width="28" height="36" rx="4" fill="none" stroke="#fff" stroke-width="2.5"/><circle cx="22" cy="18" r="6" fill="none" stroke="#fff" stroke-width="2.5"/></svg>
      <svg viewBox="0 0 44 44"><path d="M6 40 V14 L22 4 L38 14 V40 Z" fill="none" stroke="#fff" stroke-width="2.5"/><rect x="17" y="26" width="10" height="14" fill="none" stroke="#fff" stroke-width="2.5"/></svg>
      <svg viewBox="0 0 44 44"><rect x="13" y="3" width="18" height="38" rx="3" fill="none" stroke="#fff" stroke-width="2.5"/><circle cx="22" cy="35" r="2" fill="#fff"/></svg>
      <svg viewBox="0 0 44 44"><path d="M4 14 V4 H14 M30 4 H40 V14 M40 30 V40 H30 M14 40 H4 V30" fill="none" stroke="#fff" stroke-width="2.5"/><rect x="14" y="14" width="16" height="16" fill="none" stroke="#fff" stroke-width="2.5"/></svg>
      <svg viewBox="0 0 44 44"><rect x="4" y="10" width="36" height="24" rx="3" fill="none" stroke="#fff" stroke-width="2.5"/><line x1="4" y1="18" x2="40" y2="18" stroke="#fff" stroke-width="2.5"/></svg>
    </div>
  </section>

  <footer class="web">
    <svg viewBox="0 0 40 40" aria-hidden="true"><circle cx="20" cy="20" r="17" fill="none" stroke="var(--blue-light)" stroke-width="2.5"/><ellipse cx="20" cy="20" rx="7" ry="17" fill="none" stroke="var(--blue-light)" stroke-width="2"/><line x1="3" y1="20" x2="37" y2="20" stroke="var(--blue-light)" stroke-width="2"/></svg>
    <span>www.yourwebsite.com</span>
  </footer>
</main>
</body>
</html>
```